New florist business website design

Number 1 want is an easy to navigate & check out website
Needs to be beautiful and eye catching as well.
This is an online only business (no shop front)
Rustic and blush pinks, neutrals, woods, leaves
Customers need to be able to go onto my website, select something they want to buy but have the option to use a drop down box to change colours of the flowers, or add notes to make changes to the arrangement

Industry/Entity Type

Florist

Coding

Coded - Design and coding required

Number of Pages Required

5+ page

Colors
f9d9e8
fff2ec
fffefc

Requirements
Must have
• Drop down menu to take you to other pages for Arrangements, bouquets, everlasting arrangements, gifts, contact
Be able to purchase and “add to basket”
Checkout page
Nice to have
• Be able to add my own photos once I’ve taken new ones
Should not have
• Tacky images or clip art

```html
<!DOCTYPE html>
<html lang="en">
<head>
<meta charset="utf-8">
<title>Bloom &amp; Bower — Florist</title>
<link href="https://fonts.googleapis.com/css2?family=Lexend:wght@300;400;500&family=Mrs+Saint+Delafield&display=swap" rel="stylesheet">
<style>
:root{
  --ink:#1b1b1b;
  --blush:#f9d9e8;
  --peach:#fff2ec;
  --cream:#fffefc;
  --rose:#f6d5e4;
  --soft:#fdeee9;
  --muted:#5a5a5a;
  --icon-bg:#fde2d3;
}
*{box-sizing:border-box;margin:0;padding:0}
html,body{width:1200px;height:4866px;overflow:hidden}
body{position:relative;background:var(--cream);font-family:'Lexend',sans-serif;color:var(--ink)}
.abs{position:absolute}
.script{font-family:'Mrs Saint Delafield',cursive;font-weight:400}
.btn{position:absolute;border:2px solid var(--ink);border-radius:26px;background:transparent;font:500 13px 'Lexend',sans-serif;letter-spacing:1px;text-transform:uppercase;display:flex;align-items:center;justify-content:center;gap:8px;color:var(--ink)}
.topbar{left:0;top:0;width:1200px;height:26px;background:#111;color:#fff;font-size:12px;display:flex;align-items:center;justify-content:center}
.hero{left:0;top:26px;width:1200px;height:830px;background:radial-gradient(ellipse at 30% 30%,#fbe4ea 0%,#fdf1f3 45%,var(--cream) 90%)}
.nav a{position:absolute;top:61px;font-size:13px;color:var(--ink);text-decoration:none}
.brand{left:495px;top:78px;width:210px;text-align:center;font-size:28px;font-weight:300}
.brand i{display:inline-block;width:12px;height:12px;border-radius:50%;background:var(--blush);margin-right:8px;vertical-align:middle}
.hero-kicker{left:74px;top:318px;font-size:27px;letter-spacing:1px}
.hero-script{left:74px;top:340px;font-size:104px;line-height:1}
.dots{display:flex;gap:10px;align-items:center}
.dots span{width:7px;height:7px;border-radius:50%;background:#222}
.dots span.on{width:11px;height:11px;background:transparent;border:1.5px solid #d88}
.feature{top:850px;width:400px;text-align:center}
.feature .ic{width:76px;height:76px;border-radius:50%;background:var(--icon-bg);margin:0 auto;display:flex;align-items:center;justify-content:center}
.feature .s{font-size:26px;margin-top:8px;line-height:1}
.feature .t{font-size:13px;margin-top:4px}
.vline{top:888px;width:1px;height:108px;background:#999}
.sec-head{left:0;width:1200px;text-align:center}
.sec-head .s{font-size:40px;line-height:1}
.sec-head h2{font-weight:400;font-size:35px;margin-top:2px}
.sec-head .orn{width:90px;height:26px;margin:6px auto 0;border-radius:50%;background:linear-gradient(90deg,transparent,#e6d6dc,transparent)}
.bgfloral{border-radius:50%;background:radial-gradient(circle,#fbe6ee 0%,transparent 70%)}
.product{top:1304px;width:236px;height:397px;text-align:center}
.product.active{background:var(--peach);border-radius:28px}
.product .pic{width:130px;height:190px;margin:38px auto 0;border-radius:40px 40px 12px 12px}
.product .n{font-size:17px;margin-top:32px}
.product .p{font-size:36px;margin-top:2px}
.cart-btn{position:static;margin:18px auto 0;width:138px;height:40px;font-size:12px;text-transform:none;letter-spacing:0}
.arrow{top:1480px}
.welcome{left:0;top:1954px;width:1200px;height:410px;background:var(--rose)}
.welcome-pic{left:597px;top:1918px;width:603px;height:410px;border-radius:26px 0 0 26px;background:linear-gradient(135deg,#6d6a86 0%,#b7a7c6 40%,#e6c8c6 70%,#8d8060 100%)}
.welcome .s{position:absolute;left:76px;top:62px;font-size:40px}
.welcome h2{position:absolute;left:78px;top:110px;font-weight:400;font-size:37px;line-height:46px}
.welcome p,.news p{font-size:11px;line-height:18px;color:#444}
.quote{left:195px;top:2608px;width:820px;text-align:center;font-size:11.5px;line-height:18px;color:#333}
.qm{font-size:44px;font-family:Georgia,serif;line-height:1}
.post{top:3081px;width:322px;text-align:center}
.post .pic{height:226px;border-radius:30px}
.post .date{width:54px;height:54px;border-radius:50%;background:var(--peach);margin:-28px auto 0;position:relative;font-size:11px;line-height:13px;display:flex;align-items:center;justify-content:center}
.post h3{font-weight:400;font-size:25px;margin-top:14px}
.post p{font-size:11px;line-height:18px;color:#444;margin:10px 16px 0}
.post a{display:inline-block;margin-top:14px;font-size:12px;color:#888;text-decoration:underline}
.insta{top:3905px;width:210px;height:208px}
.news{left:0;top:4294px;width:1200px;height:147px;background:var(--peach)}
.field{left:675px;top:4362px;width:304px;height:36px;border:2px solid var(--ink);border-radius:20px;font-size:11px;font-style:italic;padding:10px 18px;color:#444}
.footer{left:0;top:4441px;width:1200px;height:388px;background:#fdf3f3}
.footer h4{position:absolute;top:90px;font-weight:400;font-size:26px}
.footer ul{position:absolute;list-style:none;font-size:12px;line-height:16px}
.contact li{display:flex;gap:14px;margin-bottom:12px;align-items:flex-start}
.social li{display:flex;gap:12px;align-items:center;margin-bottom:12px}
.social li i{width:14px;height:14px;border-radius:50%;background:var(--ink);display:block}
.bottombar{left:0;top:4829px;width:1200px;height:37px;background:#1a1a1a;color:#fff;font-size:12px}
.pay{top:8px;width:44px;height:24px;border-radius:4px;background:#f1f1f1}
</style>
</head>
<body>
<div class="abs topbar">Free Shipping 2 days delivery time</div>

<div class="abs hero"></div>
<div class="abs bgfloral" style="left:-60px;top:560px;width:520px;height:380px"></div>
<div class="abs bgfloral" style="left:820px;top:560px;width:420px;height:380px"></div>

<nav class="nav">
  <a style="left:72px">Home</a><a style="left:143px">Shop</a><a style="left:207px">About</a><a style="left:279px">Blogs</a><a style="left:345px">Contact</a>
</nav>
<div class="abs brand"><i></i>Bloom &amp; Bower</div>
<svg class="abs" style="left:955px;top:56px" width="28" height="28" viewBox="0 0 28 28" fill="none" stroke="#111" stroke-width="2"><circle cx="18" cy="10" r="6"/><path d="M14 14 5 23"/></svg>
<svg class="abs" style="left:1018px;top:54px" width="34" height="32" viewBox="0 0 34 32" fill="none" stroke="#111" stroke-width="2"><path d="M4 10h20l-2 18H6z"/><path d="M9 10V6a5 5 0 0 1 10 0v4"/><circle cx="25" cy="24" r="6" fill="#111"/><text x="25" y="27.5" font-size="9" fill="#fff" stroke="none" text-anchor="middle" font-family="Lexend">2</text></svg>
<svg class="abs" style="left:1088px;top:58px" width="32" height="24" viewBox="0 0 32 24" stroke="#111" stroke-width="2.5"><path d="M2 3h28M10 12h20M2 21h28"/></svg>

<div class="abs hero-kicker">GORGEOUS FLOWERS FOR YOUR</div>
<div class="abs hero-script script">Special Events</div>
<div class="btn" style="left:79px;top:494px;width:172px;height:48px">Shop Now</div>
<div class="abs" role="img" aria-label="Bouquet of red and pink gerberas, lilies and roses wrapped in white paper" style="left:580px;top:200px;width:610px;height:440px;border-radius:45% 40% 45% 50%;background:radial-gradient(circle at 45% 45%,#e33463 0%,#d6446e 35%,#ef9bbd 60%,#f4e6ef 80%,transparent 95%)"></div>
<div class="abs dots" style="left:578px;top:681px"><span></span><span class="on"></span><span></span></div>

<div class="abs feature" style="left:42px">
  <div class="ic"><svg width="36" height="36" viewBox="0 0 36 36" fill="none" stroke="#111" stroke-width="1.6"><path d="M4 17 32 5 24 31 18 20z"/><path d="M18 20 32 5"/></svg></div>
  <div class="s script">Free Shipping</div>
  <div class="t">GET A FREE DELIVERY ON ORDERS OF $200</div>
</div>
<div class="abs vline" style="left:420px"></div>
<div class="abs feature" style="left:410px">
  <div class="ic"><svg width="34" height="34" viewBox="0 0 24 24" fill="none" stroke="#111" stroke-width="1.4"><path d="M5 3h4l2 5-2.5 1.5a11 11 0 0 0 6 6L16 13l5 2v4a2 2 0 0 1-2 2A16 16 0 0 1 3 5a2 2 0 0 1 2-2"/></svg></div>
  <div class="s script">Free Support</div>
  <div class="t">24/7 CUSTOMER SERVICE</div>
</div>
<div class="abs vline" style="left:795px"></div>
<div class="abs feature" style="left:784px">
  <div class="ic" style="font-size:32px;font-weight:300">$</div>
  <div class="s script">Price Guarantee</div>
  <div class="t">WE GUARANTEE THE BEST PRICE</div>
</div>

<div class="abs bgfloral" style="left:950px;top:1030px;width:300px;height:420px"></div>
<div class="abs bgfloral" style="left:-80px;top:1650px;width:340px;height:300px"></div>
<div class="abs sec-head" style="top:1108px">
  <div class="s script">Wonderful Flowers</div>
  <h2>Feature Products</h2>
  <div class="orn" role="img" aria-label="Small leaf sprig ornament"></div>
</div>

<svg class="abs arrow" style="left:54px" width="18" height="34" viewBox="0 0 18 34" fill="none" stroke="#888" stroke-width="2"><path d="M15 3 3 17l12 14"/></svg>
<svg class="abs arrow" style="left:1120px" width="18" height="34" viewBox="0 0 18 34" fill="none" stroke="#888" stroke-width="2"><path d="M3 3l12 14L3 31"/></svg>

<div class="abs product" style="left:100px"><div class="pic" role="img" aria-label="Red carnation bouquet in pink wrap" style="background:linear-gradient(180deg,#d3203a 0%,#e0435a 55%,#f6c6d6 100%)"></div><div class="n">Name of product # 01</div><div class="p">$40</div></div>
<div class="abs product active" style="left:360px"><div class="pic" role="img" aria-label="Pink lily bouquet in pink wrap" style="background:linear-gradient(180deg,#b9477e 0%,#d67fa8 50%,#f3c6dc 100%)"></div><div class="n">Name of product # 01</div><div class="p">$40</div>
  <div class="btn cart-btn">Add To Cart <svg width="16" height="16" viewBox="0 0 16 16" fill="none" stroke="#111" stroke-width="1.4"><path d="M2 5h12l-1 9H3z"/><path d="M5 5V4a3 3 0 0 1 6 0v1"/></svg></div></div>
<div class="abs product" style="left:619px"><div class="pic" role="img" aria-label="Red tulip bunch tied with twine" style="background:linear-gradient(180deg,#d2264e 0%,#c54565 35%,#4f7a3c 70%,#2f5a2a 100%)"></div><div class="n">Name of product # 01</div><div class="p">$40</div></div>
<div class="abs product" style="left:869px"><div class="pic" role="img" aria-label="White calla lily bouquet" style="background:linear-gradient(180deg,#f4f2ea 0%,#e9ead8 50%,#8aa070 100%)"></div><div class="n">Name of product # 01</div><div class="p">$40</div></div>

<div class="btn" style="left:510px;top:1782px;width:170px;height:48px">Browse More</div>

<div class="abs welcome">
  <div class="s script">Welcome</div>
  <h2>Exclusive Design by<br>Best Florists</h2>
  <p class="abs" style="left:79px;top:226px;width:360px">Lorem Ipsum is simply dummy text of the printing and typesetting industry. Lorem Ipsum has been the industry's standard dummy text ever since the 1500s.</p>
  <div class="btn" style="left:79px;top:310px;width:172px;height:48px">Shop Now</div>
</div>
<div class="abs welcome-pic" role="img" aria-label="Wrapped bouquets of purple and pink flowers at a flower market"></div>

<div class="abs bgfloral" style="left:820px;top:2420px;width:420px;height:360px"></div>
<div class="abs bgfloral" style="left:-40px;top:2660px;width:300px;height:340px"></div>
<div class="abs sec-head" style="top:2444px">
  <div class="s script">Reviews</div>
  <h2>Testimonials</h2>
  <div class="orn" role="img" aria-label="Small leaf sprig ornament"></div>
</div>
<div class="abs quote"><span class="qm" style="position:absolute;left:-12px;top:-6px">“</span>Lorem Ipsum is simply dummy text of the printing and typesetting industry. Lorem Ipsum has been the industry's standard dummy text ever since the 1500s, when an unknown printer took a galley of type and scrambled it to make a type specimen book. It has survived not only five centuries, but also the leap into electronic typesetting, remaining essentially unchanged.<span class="qm" style="position:absolute;right:-12px;top:30px">”</span></div>
<div class="abs script" style="left:0;width:1200px;text-align:center;top:2686px;font-size:36px">Elena</div>
<div class="abs dots" style="left:578px;top:2752px"><span></span><span class="on"></span><span></span></div>

<div class="abs sec-head" style="top:2894px">
  <div class="s script">Articles</div>
  <h2>Blog Posts</h2>
  <div class="orn" role="img" aria-label="Small leaf sprig ornament"></div>
</div>
<div class="abs post" style="left:79px"><div class="pic" role="img" aria-label="Pink cherry blossom branches on white" style="background:linear-gradient(135deg,#f1f0ee 0%,#eab6c6 45%,#e58aa6 70%,#eeeaea 100%)"></div><div class="date">june<br>2,2021</div><h3>Artcle title # 01</h3><p>Lorem Ipsum is simply dummy text of the printing and typesetting industry. Lorem Ipsum has been the industry's standard dummy text ever since the 1500s.</p><a>Read More »</a></div>
<div class="abs post" style="left:438px"><div class="pic" role="img" aria-label="Bright purple chrysanthemums" style="background:linear-gradient(135deg,#c24bd1 0%,#9f2bb6 50%,#d773de 100%)"></div><div class="date">june<br>2,2021</div><h3>Artcle title # 02</h3><p>Lorem Ipsum is simply dummy text of the printing and typesetting industry. Lorem Ipsum has been the industry's standard dummy text ever since the 1500s.</p><a>Read More »</a></div>
<div class="abs post" style="left:799px"><div class="pic" role="img" aria-label="Orange and lilac dahlias" style="background:linear-gradient(135deg,#f0a03a 0%,#e8823a 40%,#c996cf 75%,#6d4a2a 100%)"></div><div class="date">june<br>2,2021</div><h3>Artcle title # 03</h3><p>Lorem Ipsum is simply dummy text of the printing and typesetting industry. Lorem Ipsum has been the industry's standard dummy text ever since the 1500s.</p><a>Read More »</a></div>
<div class="btn" style="left:512px;top:3564px;width:170px;height:48px">Browse More</div>

<div class="abs bgfloral" style="left:-40px;top:3540px;width:320px;height:300px"></div>
<div class="abs bgfloral" style="left:880px;top:3560px;width:340px;height:280px"></div>
<div class="abs sec-head" style="top:3736px">
  <div class="s script">Follow us on</div>
  <h2>Snapgram</h2>
  <div class="orn" role="img" aria-label="Small leaf sprig ornament"></div>
</div>
<div class="abs insta" style="left:70px" role="img" aria-label="Pale peach peony bouquet" style2="" ></div>
<div class="abs insta" style="left:70px;background:linear-gradient(135deg,#f3e4dc,#e8cfc4,#c9b7ae)" role="img" aria-label="Pale peach peony bouquet"></div>
<div class="abs insta" style="left:280px;background:linear-gradient(135deg,#5d6b3a,#8fa9d8,#e6ecef)" role="img" aria-label="Blue and white bridal bouquet"></div>
<div class="abs insta" style="left:490px;background:linear-gradient(135deg,#d8cbe5,#7f61c0,#4d3b7e)" role="img" aria-label="Purple flower bouquet"></div>
<div class="abs insta" style="left:700px;background:linear-gradient(135deg,#f5b7b9,#ee9aa6,#dd7e92)" role="img" aria-label="Pink rose bouquet"></div>
<div class="abs insta" style="left:910px;width:209px;background:linear-gradient(135deg,#5e3a4e,#a05bb0,#e4d7e6)" role="img" aria-label="Purple and magenta bridal bouquet"></div>
<div class="btn" style="left:509px;top:4164px;width:170px;height:48px">Follow Us <svg width="20" height="20" viewBox="0 0 20 20" fill="none" stroke="#111" stroke-width="1.5"><rect x="2" y="2" width="16" height="16" rx="4"/><circle cx="10" cy="10" r="4"/></svg></div>

<div class="abs news">
  <div class="abs" style="left:74px;top:40px;font-size:25px">Join us for our latest news updates</div>
  <p class="abs" style="left:74px;top:86px;width:540px">Lorem Ipsum is simply dummy text of the printing and typesetting industry. Lorem Ipsum has been the industry's standard dummy text ever since the 1500s.</p>
</div>
<div class="abs field">Email Address</div>
<div class="btn" style="left:987px;top:4362px;width:132px;height:36px;font-size:12px">Subscribe</div>

<div class="abs footer">
  <div class="abs" style="left:76px;top:150px;font-size:38px;font-weight:300;display:flex;align-items:center;gap:12px"><span style="width:18px;height:18px;border-radius:50%;background:var(--blush);display:block"></span>Bloom &amp; Bower</div>
  <h4 style="left:467px">Quick links</h4>
  <ul style="left:469px;top:176px;font-weight:500">
    <li>Home</li><li>Shop</li><li>About</li><li>Blogs</li><li>Contact</li><li>Arrangement</li><li>bouquets</li><li>everlasting arrangements</li><li>gifts</li>
  </ul>
  <h4 style="left:705px">Contact info.</h4>
  <ul class="contact" style="left:710px;top:176px">
    <li><svg width="12" height="14" viewBox="0 0 12 14"><path d="M6 0a5 5 0 0 1 5 5c0 4-5 9-5 9S1 9 1 5a5 5 0 0 1 5-5z" fill="#111"/><circle cx="6" cy="5" r="2" fill="#fdf3f3"/></svg><span>214 Willow Lane<br>Fernvale, CA 90210</span></li>
    <li><svg width="12" height="12" viewBox="0 0 24 24" fill="#111"><path d="M5 2h4l2 5-2.5 1.5a11 11 0 0 0 6 6L16 12l5 2v4a2 2 0 0 1-2 2A17 17 0 0 1 3 4a2 2 0 0 1 2-2"/></svg><span>(+00) 555 010 246</span></li>
    <li><svg width="12" height="10" viewBox="0 0 12 10"><rect width="12" height="10" fill="#111"/><path d="M0 0l6 5 6-5" stroke="#fdf3f3" fill="none"/></svg><span>hello@bloomandbower.com</span></li>
  </ul>
  <h4 style="left:979px">Social Links</h4>
  <ul class="social" style="left:986px;top:176px">
    <li><i></i>Friendbook</li><li><i></i>Chirper</li><li><i></i>Mailbox</li><li><i></i>Snapgram</li><li><i></i>Pinboard</li>
  </ul>
</div>

<div class="abs bottombar">
  <div class="abs" style="left:72px;top:11px">Copyright © 2021 Bloom &amp; Bower &nbsp;/&nbsp; Privacy Policy</div>
  <div class="abs pay" style="left:886px"></div>
  <div class="abs pay" style="left:934px"></div>
  <div class="abs pay" style="left:982px"></div>
  <div class="abs pay" style="left:1030px"></div>
  <div class="abs pay" style="left:1078px;background:#9ec3e8"></div>
</div>
</body>
</html>
```